I need a fresh looking, exciting and loaded design for Full service Restaurant

We need a web design for our restaurant, which offers full service Pakistani and Indian food in PA, USA. Design should be elegant, simplified so customers can navigate easily and order food online for catering as well as delivery. We need loads of pictures and room to grow. I already have a web address via vemrilo.com. It should include SSL and e-commerce for ordering food.
Be original and be creative and make it a fun site :)

```html
<!DOCTYPE html>
<html lang="en">
<head>
<meta charset="utf-8">
<title>Saffron Court – Pakistani &amp; Indian Restaurant</title>
<link href="https://fonts.googleapis.com/css2?family=Great+Vibes&family=Oswald:wght@400;600&family=Open+Sans:wght@400;600&display=swap" rel="stylesheet">
<style>
:root{
  --red:#c8202a;
  --red-dark:#8e1a20;
  --green:#3f8a2e;
  --ink:#2b2b2b;
  --muted:#777;
  --white:#fff;
  --paper:#ffffff;
}
*{box-sizing:border-box;margin:0;padding:0}
html,body{width:669px;height:1200px;overflow:hidden;background:var(--paper)}
body{position:relative;font-family:"Open Sans",sans-serif;color:var(--ink)}
.abs{position:absolute}
.photo{position:absolute}

/* header */
.brand{left:70px;top:12px;display:flex;align-items:center;gap:8px}
.brand-mark{width:30px;height:30px;border-radius:50%;background:var(--green)}
.brand-name{font-family:"Oswald",sans-serif;font-weight:600;font-size:22px;color:var(--red);line-height:1}
.brand-tag{position:absolute;left:38px;top:30px;font-size:7px;color:var(--muted);white-space:nowrap}
.contact{right:72px;top:20px;font-size:8px;color:var(--muted)}
.contact .phone{font-size:12px;color:var(--green);font-weight:600;margin-top:3px;display:flex;align-items:center;gap:4px}

.main-nav{left:70px;top:66px;width:545px;height:19px;background:var(--red);display:flex;align-items:center;z-index:3}
.main-nav a{font-size:7px;color:var(--white);text-decoration:none;padding:0 8px;line-height:19px;text-transform:uppercase}
.main-nav a.active{background:var(--green)}
.main-nav .social{margin-left:auto;display:flex;gap:14px;padding-right:14px}
.social span{font-size:8px;color:var(--white);font-weight:600}

/* hero */
.hero{left:0;top:86px;width:669px;height:250px;background:radial-gradient(ellipse at 55% 55%,#c89a5a 0%,#8a5a2c 45%,#3a2212 100%)}
.hero-title{left:0;width:669px;top:178px;text-align:center;font-family:"Oswald",sans-serif;font-weight:600;font-size:32px;color:var(--white);letter-spacing:1px;line-height:1}
.hero-sub{left:0;width:669px;top:218px;text-align:center;font-size:7px;color:var(--white)}
.hero-rule{left:304px;top:236px;width:60px;height:1px;background:var(--white)}
.btn{position:absolute;font-size:7.5px;text-transform:uppercase;color:var(--white);text-align:center;line-height:20px;height:20px}
.btn-outline{left:248px;top:268px;width:80px;border:1px solid var(--white);line-height:18px}
.btn-solid{left:340px;top:268px;width:80px;background:var(--red)}
.dots{left:593px;top:263px;display:flex;flex-direction:column;gap:4px}
.dots i{width:5px;height:5px;border-radius:50%;background:var(--white);display:block}
.scroll-down{left:322px;top:322px;width:26px;height:26px;z-index:2}

/* section type */
.script{font-family:"Great Vibes",cursive;color:var(--red);font-size:28px;line-height:1}
.heading{font-family:"Oswald",sans-serif;font-weight:600;font-size:26px;letter-spacing:2px;line-height:1;color:var(--ink)}
.copy{font-size:7px;line-height:1.55;color:var(--muted)}
.link{font-size:7px;font-weight:600;color:var(--red);text-transform:uppercase;border-bottom:1px solid var(--red);padding-bottom:2px}

/* story */
.story-welcome{left:160px;top:356px}
.story-heading{left:134px;top:384px}
.story-copy{left:75px;top:422px;width:280px}
.story-link{left:178px;top:474px}

/* recipes */
.recipes-label{left:241px;top:600px;width:183px;text-align:center}
.recipes-label .script{color:var(--white);font-size:22px}
.recipes-label .heading{color:var(--white);font-size:20px}

/* menu */
.menu-discover{left:410px;top:750px}
.menu-heading{left:432px;top:782px}
.menu-copy{left:336px;top:816px;width:280px;text-align:center}
.menu-link{left:432px;top:870px}

/* newsletter */
.newsletter{left:0;top:956px;width:669px;height:190px;background:linear-gradient(180deg,#3a302a 0%,#2a2420 60%,#4a3a2c 100%)}
.news-title{left:0;width:669px;top:1002px;text-align:center;font-family:"Oswald",sans-serif;font-weight:600;font-size:24px;letter-spacing:3px;color:var(--white)}
.news-form{left:188px;top:1056px;display:flex}
.news-input{width:220px;height:20px;background:var(--red-dark);color:#e8c9c9;font-size:7px;line-height:20px;padding-left:8px}
.news-btn{width:62px;height:20px;margin-left:3px;background:var(--red);color:var(--white);font-size:7px;line-height:20px;text-align:center;text-transform:uppercase;font-weight:600}
.news-social{left:0;width:669px;top:1096px;display:flex;justify-content:center;gap:20px}
.news-social span{color:var(--white);font-size:11px;font-weight:600}

/* footer */
.footer-nav{left:0;width:669px;top:1152px;display:flex;justify-content:center;gap:16px}
.footer-nav a{font-size:7px;text-transform:uppercase;color:var(--ink);text-decoration:none}
.copyright{left:0;width:669px;top:1176px;text-align:center;font-size:6.5px;color:var(--muted);border-top:1px solid #e2e2e2;padding-top:6px}
</style>
</head>
<body>

<header>
  <div class="abs brand">
    <span class="brand-mark"></span>
    <span class="brand-name">Saffron Court</span>
    <span class="brand-tag">Fine Pakistani &amp; Indian Cuisine</span>
  </div>
  <div class="abs contact">
    Call for free delivery
    <div class="phone">
      <svg width="9" height="9" viewBox="0 0 24 24"><path fill="#3f8a2e" d="M6.6 10.8c1.4 2.8 3.8 5.1 6.6 6.6l2.2-2.2c.3-.3.7-.4 1-.2 1.1.4 2.3.6 3.6.6.6 0 1 .4 1 1V20c0 .6-.4 1-1 1C10.6 21 3 13.4 3 4c0-.6.4-1 1-1h3.5c.6 0 1 .4 1 1 0 1.3.2 2.5.6 3.6.1.3 0 .7-.2 1z"/></svg>
      1 - 080 555 0142
    </div>
  </div>
  <nav class="abs main-nav">
    <a class="active" href="#">Home</a><a href="#">About us</a><a href="#">Menus</a><a href="#">Services</a><a href="#">Store</a><a href="#">Testimonials</a><a href="#">Contact us</a>
    <div class="social"><span>f</span><span>G+</span><span>t</span></div>
  </nav>
</header>

<section>
  <div class="photo hero" role="img" aria-label="Photo of a curry dish served in a copper bowl with rice"></div>
  <h1 class="abs hero-title">Saffron Court</h1>
  <p class="abs hero-sub">Authentic taste since 1998</p>
  <span class="abs hero-rule"></span>
  <span class="btn btn-outline">Book a table</span>
  <span class="btn btn-solid">See the menu</span>
  <div class="abs dots"><i></i><i></i><i></i></div>
  <svg class="abs scroll-down" viewBox="0 0 26 26"><circle cx="13" cy="13" r="13" fill="#fff"/><path d="M8 11l5 5 5-5" fill="none" stroke="#444" stroke-width="1.6"/></svg>
</section>

<section>
  <div class="abs script story-welcome">Welcome</div>
  <h2 class="abs heading story-heading">OUR STORY</h2>
  <p class="abs copy story-copy">Arthur Pemberton, a Latin professor at Halden College in Virginia, looked up one of the more obscure Latin words, consectetur, from a Lorem Ipsum passage, and going through the cites of the word in classical literature, discovered the undoubtable source.</p>
  <span class="abs link story-link">About us</span>
  <div class="photo" style="left:412px;top:352px;width:60px;height:165px;background:linear-gradient(160deg,#c9a26a,#7b5a2e)" role="img" aria-label="Photo of grilled kebabs with rice"></div>
  <div class="photo" style="left:479px;top:352px;width:116px;height:80px;background:linear-gradient(160deg,#a8242c,#5a1418)" role="img" aria-label="Photo of sliced cured meats"></div>
  <div class="photo" style="left:479px;top:437px;width:116px;height:80px;background:linear-gradient(160deg,#d8c9a8,#8f6d3a)" role="img" aria-label="Photo of a plated dish with herbs"></div>
</section>

<section>
  <div class="photo" style="left:56px;top:547px;width:178px;height:162px;background:linear-gradient(160deg,#b89a5c,#5c4a2a)" role="img" aria-label="Photo of bowls of curry on a table"></div>
  <div class="photo" style="left:241px;top:547px;width:183px;height:162px;background:radial-gradient(circle at 50% 50%,#b5452a,#3a1a10)" role="img" aria-label="Photo of meatballs in a skillet"></div>
  <div class="abs recipes-label"><div class="script">Favourite</div><div class="heading">RECIPES</div></div>
  <div class="photo" style="left:430px;top:547px;width:183px;height:162px;background:linear-gradient(160deg,#e6a07a,#9a4a2a)" role="img" aria-label="Photo of grilled salmon fillets"></div>
</section>

<section>
  <div class="photo" style="left:56px;top:733px;width:132px;height:100px;background:linear-gradient(160deg,#a3441e,#5e2810)" role="img" aria-label="Photo of a spicy curry in a bowl"></div>
  <div class="photo" style="left:196px;top:733px;width:128px;height:100px;background:linear-gradient(160deg,#e9e2d4,#a06a3a)" role="img" aria-label="Photo of fried fish with lemon"></div>
  <div class="photo" style="left:56px;top:840px;width:132px;height:98px;background:linear-gradient(160deg,#6a5a2e,#c9a24a)" role="img" aria-label="Photo of a rice dish with garnish"></div>
  <div class="photo" style="left:196px;top:840px;width:128px;height:98px;background:linear-gradient(160deg,#f0e6d6,#c99a5a)" role="img" aria-label="Photo of sweet dumplings on a plate"></div>
  <div class="abs script menu-discover">Discover</div>
  <h2 class="abs heading menu-heading">MENU</h2>
  <p class="abs copy menu-copy">Arthur Pemberton, a Latin professor at Halden College in Virginia, looked up one of the more obscure Latin words, consectetur, from a Lorem Ipsum passage, and going through the cites of the word in classical literature, discovered the undoubtable source.</p>
  <span class="abs link menu-link">View the full menu</span>
</section>

<section>
  <div class="photo newsletter" role="img" aria-label="Dark photo of a rice dish in a serving bowl"></div>
  <h2 class="abs news-title">NEWSLETTER</h2>
  <div class="abs news-form"><span class="news-input">Enter Email Id</span><span class="news-btn">Subscribe</span></div>
  <div class="abs news-social"><span>f</span><span>t</span><span>G+</span></div>
</section>

<footer>
  <nav class="abs footer-nav"><a href="#">Home</a><a href="#">About us</a><a href="#">Menus</a><a href="#">Services</a><a href="#">Store</a><a href="#">Testimonials</a><a href="#">Contact us</a></nav>
  <p class="abs copyright">© 2016 www.vemrilo.com</p>
</footer>

</body>
</html>
```